Lorvex Tilo medical cannibis cultivation company

tag - Tilo rise
Lorvex Tilo medical cannabis cultivation - logo is selected- can we please see bold examples with our selection. We are mainly dealing with medical companies and professionals. We would like to be stand out in the crowd with our designs. Welcome any and all attempts. Thanks

Target Market(s)

Medical and Professional

Industry/Entity Type

Medical And Science

Font styles to use
Sans Serif

Colors

Designer to choose colors to be used in the design.

Requirements
Must have
• Bright colour and be bold- Love the teal and magenta that is currently on the dark background design.
Nice to have
• shading and the 3D affect- The shadowed appearance.
Should not have
• Anything related to illegal activity or un professional manners

```html
<!DOCTYPE html>
<html lang="en">
<head>
<meta charset="utf-8">
<title>Lorvex Tilo — Business Card</title>
<link href="https://fonts.googleapis.com/css2?family=Roboto:wght@400;500;700&display=swap" rel="stylesheet">
<style>
  :root {
    --backdrop: #e4e4e4;
    --card: #000000;
    --magenta: #9d4a9e;
    --teal: #14a9e2;
    --silver: #8c9197;
    --text-light: #e6e6e6;
    --band-text: #2a1a2b;
  }
  * { margin: 0; padding: 0; box-sizing: border-box; }
  html, body {
    width: 1125px; height: 1200px; overflow: hidden;
    background: var(--backdrop);
    font-family: "Roboto", Arial, sans-serif;
  }
  .canvas { position: relative; width: 1125px; height: 1200px; }
  .card {
    position: absolute; left: 162px; width: 800px; height: 457px;
    background: var(--card); border-radius: 26px; overflow: hidden;
    box-shadow: 0 14px 30px rgba(0,0,0,0.35);
  }
  .card--front { top: 95px; }
  .card--back { top: 612px; }

  .brand { position: absolute; text-align: center; }
  .card--front .brand { left: 40px; top: 86px; width: 400px; }
  .card--back .brand { left: 200px; top: 108px; width: 400px; }
  .brand__mark {
    display: block; margin: 0 auto 20px; width: 150px; height: 150px;
    border: 4px solid var(--silver); border-radius: 50%;
  }
  .brand__name {
    font-weight: 700; font-size: 46px; letter-spacing: 1px;
    color: var(--teal); line-height: 1; text-transform: uppercase;
  }
  .brand__tag {
    display: flex; align-items: center; justify-content: center; gap: 8px;
    margin-top: 6px; font-size: 20px; letter-spacing: 2px;
    color: var(--silver); text-transform: uppercase;
  }
  .brand__tag::before, .brand__tag::after {
    content: ""; width: 56px; height: 2px; background: var(--silver);
  }

  .divider {
    position: absolute; left: 437px; top: 75px; width: 2px; height: 262px;
    background: linear-gradient(to bottom, transparent, #5a5a5a 20%, #5a5a5a 80%, transparent);
  }
  .contact { position: absolute; left: 480px; top: 86px; color: var(--text-light); }
  .contact__name { font-weight: 700; font-size: 29px; color: var(--magenta); line-height: 1.05; text-transform: uppercase; }
  .contact__role { font-weight: 500; font-size: 20px; color: var(--teal); margin-top: 2px; }
  .contact__address { font-size: 19px; line-height: 24px; margin-top: 16px; }
  .contact__list { list-style: none; margin-top: 14px; }
  .contact__item { display: flex; align-items: center; gap: 12px; font-size: 19px; height: 25.5px; }
  .contact__item svg { width: 18px; height: 18px; fill: var(--magenta); flex: none; }

  .web-band {
    position: absolute; left: 0; top: 390px; width: 100%; height: 38px;
    background: var(--magenta); color: var(--band-text);
    font-size: 19px; letter-spacing: 10.5px; text-align: center; line-height: 38px;
  }
</style>
</head>
<body>
<main class="canvas">
  <section class="card card--front">
    <div class="brand">
      <span class="brand__mark"></span>
      <div class="brand__name">Lorvex Tilo</div>
      <div class="brand__tag">Tilo rise</div>
    </div>
    <div class="divider"></div>
    <div class="contact">
      <div class="contact__name">Mara Velden</div>
      <div class="contact__role">CEO/FOUNDER</div>
      <div class="contact__address">4120 Harlow Street<br>Fairbend, Oregon 97210</div>
      <ul class="contact__list">
        <li class="contact__item">
          <svg viewBox="0 0 24 24"><path d="M6.6 10.8a15.1 15.1 0 0 0 6.6 6.6l2.2-2.2c.3-.3.7-.4 1-.2 1.1.4 2.3.6 3.6.6.6 0 1 .4 1 1V20c0 .6-.4 1-1 1A17 17 0 0 1 3 4c0-.6.4-1 1-1h3.5c.6 0 1 .4 1 1 0 1.3.2 2.5.6 3.6.1.3 0 .7-.2 1z"/></svg>
          503 214 7781</li>
        <li class="contact__item">
          <svg viewBox="0 0 24 24"><path d="M7 1h10a2 2 0 0 1 2 2v18a2 2 0 0 1-2 2H7a2 2 0 0 1-2-2V3a2 2 0 0 1 2-2zm0 3v14h10V4zm5 15.5a1 1 0 1 0 0 2 1 1 0 0 0 0-2z"/></svg>
          503 618 2290</li>
        <li class="contact__item">
          <svg viewBox="0 0 24 24"><path d="M6 2h12v6H6zM3 9h18a2 2 0 0 1 2 2v7h-4v4H5v-4H1v-7a2 2 0 0 1 2-2zm4 7v4h10v-4z"/></svg>
          503 409 3365</li>
        <li class="contact__item">
          <svg viewBox="0 0 24 24"><path d="M2 5h20v14H2zm2 2v.5l8 5 8-5V7zm0 2.8V17h16V9.8l-8 5z"/></svg>
          mara@lorvextilo.com</li>
      </ul>
    </div>
    <div class="web-band">www.lorvextilorise.com</div>
  </section>

  <section class="card card--back">
    <div class="brand">
      <span class="brand__mark"></span>
      <div class="brand__name">Lorvex Tilo</div>
      <div class="brand__tag">Tilo rise</div>
    </div>
  </section>
</main>
</body>
</html>
```